Kelvor Engineers: Why you should hire us keepsake

New design. Open to plastic cards. We are an engineering firm that designs cell phone towers and commercial buildings. Please check out our website www.kelvorstruct.com for more details. We want people to remember our card and for it to be useful if possible. We want the same look and feel on these cards to be translated to other marketing material we may need such as brochures.

Target Market(s)

Architects, Developers and Telecommunication Carriers

Industry/Entity Type

Engineering

Contact Information for Business Card

Card with our company colors, logo, and innovative design with elements related to our industry.

Font styles to use
Sans Serif

Colors
9bcb3c
abd036
0255a3

Requirements
Must have
• Sleek and hip design
Nice to have
• Bright lime green and navy coloring that pops with an innovative design.
Should not have
• A basic and boring design

```html
<!DOCTYPE html>
<html lang="en">
<head>
<meta charset="utf-8">
<title>Kelvor Engineers – Business Card</title>
<link href="https://fonts.googleapis.com/css2?family=Poppins:wght@400;600;800&display=swap" rel="stylesheet">
<style>
  :root {
    --navy: #1f3a7a;
    --navy-deep: #17295c;
    --lime: #c7d12e;
    --white: #ffffff;
    --stage: #e9ebef;
    --ink-soft: #3a4a78;
  }
  html, body {
    margin: 0;
    width: 1200px;
    height: 930px;
    overflow: hidden;
    background: var(--stage);
    font-family: "Poppins", sans-serif;
  }
  .card {
    position: absolute;
    left: 240px;
    width: 720px;
    height: 411px;
    border-radius: 22px;
    overflow: hidden;
    box-shadow: 0 6px 18px rgba(0,0,0,0.18);
  }
  /* Front */
  .card--front { top: 40px; background: var(--navy); }
  .team-photo {
    position: absolute; inset: 0;
    background: linear-gradient(160deg, #2c4a8f 0%, #253f80 45%, #1e3670 100%);
  }
  .front-wordmark {
    position: absolute;
    left: 60px; top: 150px;
    font-weight: 800;
    font-size: 64px;
    line-height: 1;
    color: var(--lime);
    letter-spacing: -1px;
  }
  .city-list {
    position: absolute;
    left: 60px; bottom: 48px;
    font-weight: 400;
    font-size: 20px;
    letter-spacing: 1.5px;
    color: var(--white);
  }
  .city-list .sep { color: var(--lime); margin: 0 8px; }

  /* Back */
  .card--back { top: 480px; background: var(--white); }
  .back-wordmark {
    position: absolute;
    left: 50px; top: 150px;
    font-weight: 800;
    font-size: 42px;
    line-height: 1.05;
    color: var(--lime);
    letter-spacing: -0.5px;
  }
  .contact {
    position: absolute;
    left: 400px; top: 52px;
    width: 320px;
    color: var(--navy);
  }
  .contact__head {
    display: flex;
    align-items: center;
    gap: 14px;
  }
  .contact__name { font-weight: 600; font-size: 19px; margin: 0; white-space: nowrap; }
  .contact__head-rule { flex: 1; height: 1.5px; background: var(--navy); }
  .contact__title { font-weight: 400; font-size: 15px; color: var(--lime); margin: 0 0 8px; }
  .contact__rule { width: 230px; height: 1.5px; background: var(--navy); margin-bottom: 10px; }
  .contact__list { list-style: none; margin: 0; padding: 0; }
  .contact__list li {
    display: flex; align-items: center; gap: 10px;
    font-size: 15px; line-height: 24px; color: var(--ink-soft);
  }
  .contact__list svg { width: 12px; height: 12px; flex: none; }
  .swoosh { position: absolute; inset: 0; }
  .tagline {
    font-family: "Poppins", sans-serif;
    font-size: 12px;
    letter-spacing: 1.6px;
    fill: var(--white);
  }
</style>
</head>
<body>

<section class="card card--front">
  <div class="team-photo" role="img" aria-label="Navy-tinted team photo of three staff members standing outdoors"></div>
  <div class="front-wordmark">Kelvor Engineers</div>
  <div class="city-list">ATLANTA<span class="sep">|</span>CHARLOTTE<span class="sep">|</span>HOUSTON<span class="sep">|</span>SAN ANTONIO</div>
</section>

<section class="card card--back">
  <div class="back-wordmark">Kelvor<br>Engineers</div>
  <div class="contact">
    <div class="contact__head">
      <p class="contact__name">Dana Holloway Reyes</p>
      <div class="contact__head-rule"></div>
    </div>
    <p class="contact__title">Director</p>
    <div class="contact__rule"></div>
    <ul class="contact__list">
      <li><svg viewBox="0 0 12 12"><path d="M2.5 1 L4.5 1 L5 3.5 L3.8 4.5 Q5 7 7.5 8.2 L8.5 7 L11 7.5 L11 9.5 Q10.5 11 9 11 Q1 10 1 3 Q1 1.5 2.5 1Z" fill="var(--lime)"/></svg>404.555.0182</li>
      <li><svg viewBox="0 0 12 12"><rect x="3" y="0.8" width="6" height="10.4" rx="1.2" fill="none" stroke="var(--lime)" stroke-width="1.4"/><circle cx="6" cy="9" r="0.8" fill="var(--lime)"/></svg>706.555.0147</li>
      <li><svg viewBox="0 0 12 12"><rect x="1" y="2.5" width="10" height="7" fill="none" stroke="var(--lime)" stroke-width="1.3"/><path d="M1 2.5 L6 6.5 L11 2.5" fill="none" stroke="var(--lime)" stroke-width="1.3"/></svg>dreyes@kelvorstruct.com</li>
      <li><svg viewBox="0 0 12 12"><circle cx="6" cy="6" r="5" fill="none" stroke="var(--lime)" stroke-width="1.2"/><ellipse cx="6" cy="6" rx="2.2" ry="5" fill="none" stroke="var(--lime)" stroke-width="1"/><path d="M1 6 H11" stroke="var(--lime)" stroke-width="1"/></svg>www.kelvorstruct.com</li>
    </ul>
  </div>

  <svg class="swoosh" viewBox="0 0 720 411">
    <path d="M0,352 C260,350 480,292 720,228" fill="none" stroke="var(--lime)" stroke-width="5"/>
    <path d="M0,364 C260,362 490,306 720,244 L720,292 C520,346 300,390 0,390 Z" fill="var(--navy)"/>
    <path d="M0,397 C280,397 450,368 590,330 C450,380 260,411 0,411 Z" fill="var(--lime)"/>
    <path id="tagline-path" d="M0,377 C260,376 505,326 720,268" fill="none"/>
    <text class="tagline" dominant-baseline="middle"><textPath href="#tagline-path" startOffset="448">MULTI-DISCIPLINE ENGINEERING</textPath></text>
  </svg>
</section>

</body>
</html>
```